Email Signature

Hello,

We need an editable file so that when new staff start or someone is promoted we can easily edit this file.

The previous designer has not kept the email signatures uniform they should all be as per Dale Fenwick signature.

I also need the Omar Qadri changes as below -
Senior Mechanical Engineer
Email should be omar.qadri@tovek.com.au

You can see the Glen Harper file is different I need this the same as Dale Fenwick format but with details changed.

Also need a new one with details as per below -
Kevin Doyle
Commercial Manager
0417 263 519
kevin.doyle@tovek.com.au
www.tovek.com.au

```html
<!DOCTYPE html>
<html lang="en">
<head>
<meta charset="utf-8">
<title>Email Signature – Glen Harper</title>
<link rel="stylesheet" href="https://fonts.googleapis.com/css2?family=Roboto:wght@700&family=Mulish:wght@400&family=Exo+2:wght@800&display=swap">
<style>
  :root {
    --page-bg: #e6e6e6;
    --card-bg: #ffffff;
    --sky: #35c3f2;
    --brand-blue: #2a8bd4;
    --band-blue: #1b8fdb;
    --band-green: #8dc63f;
    --ink: #222222;
    --white: #ffffff;
  }
  * { margin: 0; padding: 0; box-sizing: border-box; }
  html, body {
    width: 1200px; height: 533px; overflow: hidden;
    background: var(--page-bg);
  }
  .canvas { position: relative; width: 1200px; height: 533px; }
  .heading {
    position: absolute; top: 38px; left: 0; width: 1200px;
    text-align: center;
    font: 700 57px/1 "Roboto", Arial, sans-serif;
    color: var(--sky);
  }
  .signature {
    position: absolute; left: 45px; top: 131px; width: 1038px; height: 346px;
    background: var(--card-bg);
    box-shadow: 0 -4px 14px rgba(0,0,0,.18);
  }
  .person { position: absolute; left: 31px; top: 40px; }
  .person-name {
    font: 700 48px/1 "Roboto", Arial, sans-serif;
    color: var(--brand-blue);
  }
  .person-title {
    margin-top: 12px;
    font: 400 25px/1 "Mulish", Arial, sans-serif;
    color: var(--ink);
  }
  .contact-list { position: absolute; left: 31px; top: 150px; list-style: none; }
  .contact-item {
    display: flex; align-items: center; height: 41px;
    font: 400 27px/1 "Mulish", Arial, sans-serif;
    color: var(--ink);
  }
  .contact-icon { width: 32px; height: 32px; margin-right: 12px; flex: none; }
  .brand {
    position: absolute; left: 458px; top: 40px; width: 560px; height: 240px;
    display: flex; align-items: center; justify-content: center; gap: 22px;
  }
  .brand-dot {
    width: 70px; height: 70px; border-radius: 50%;
    background: var(--sky); flex: none;
  }
  .brand-name {
    font: 700 120px/1 "Roboto", Arial, sans-serif;
    color: var(--sky);
  }
  .footer-band { position: absolute; left: 0; bottom: 0; width: 1038px; height: 38px; }
</style>
</head>
<body>
<div class="canvas">
  <h1 class="heading">Editable file</h1>

  <section class="signature">
    <div class="person">
      <p class="person-name">Glen Harper</p>
      <p class="person-title">Director</p>
    </div>

    <ul class="contact-list">
      <li class="contact-item">
        <svg class="contact-icon" viewBox="0 0 32 32" aria-hidden="true">
          <circle cx="16" cy="16" r="16" fill="var(--brand-blue)"/>
          <path d="M11 8c1 0 2 3 2 4s-2 1-1 3 3 4 4 4 2-2 3-1 3 2 3 3-2 3-4 3-6-2-8-5-3-6-2-8 2-3 3-3z" fill="var(--white)"/>
        </svg>
        <span>0438 615 207</span>
      </li>
      <li class="contact-item">
        <svg class="contact-icon" viewBox="0 0 32 32" aria-hidden="true">
          <circle cx="16" cy="16" r="16" fill="var(--brand-blue)"/>
          <rect x="8" y="10" width="16" height="12" rx="2" fill="var(--white)"/>
          <path d="M8 11l8 6 8-6" fill="none" stroke="var(--brand-blue)" stroke-width="1.6"/>
        </svg>
        <span>glen.harper@tovek.com.au</span>
      </li>
      <li class="contact-item">
        <svg class="contact-icon" viewBox="0 0 32 32" aria-hidden="true">
          <circle cx="16" cy="16" r="16" fill="var(--brand-blue)"/>
          <circle cx="16" cy="16" r="9" fill="var(--white)"/>
          <path d="M11 11c3 0 4 2 3 4s-3 1-3 4M18 9c0 3 3 2 4 5M17 21c1-2 3-3 4-1" fill="none" stroke="var(--brand-blue)" stroke-width="1.8"/>
        </svg>
        <span>www.tovek.com.au</span>
      </li>
    </ul>

    <div class="brand">
      <span class="brand-dot" aria-hidden="true"></span>
      <span class="brand-name">Tovek</span>
    </div>

    <svg class="footer-band" viewBox="0 0 1038 38">
      <rect width="1038" height="38" fill="var(--band-green)"/>
      <polygon points="0,0 675,0 662,38 0,38" fill="var(--band-blue)"/>
      <path d="M31 8a7 7 0 0 1 7 7c0 6-7 13-7 13s-7-7-7-13a7 7 0 0 1 7-7z" fill="var(--white)"/>
      <circle cx="31" cy="15" r="2.6" fill="var(--band-blue)"/>
      <text x="47" y="28" textLength="600" lengthAdjust="spacingAndGlyphs"
            font-family="'Exo 2', Arial, sans-serif" font-weight="800" font-size="23" fill="var(--white)">14/ 210 Carrow Road, Banyo QLD 4014</text>
      <text x="710" y="29" textLength="210" lengthAdjust="spacingAndGlyphs"
            font-family="'Exo 2', Arial, sans-serif" font-weight="800" font-size="23" fill="var(--white)">1300 452 918</text>
      <circle cx="945" cy="19" r="9.5" fill="var(--band-blue)"/>
      <circle cx="971" cy="19" r="9.5" fill="var(--band-blue)"/>
      <circle cx="996" cy="19" r="9.5" fill="var(--band-blue)"/>
    </svg>
  </section>
</div>
</body>
</html>
```